KLV Plant Services

We are a heavy diesel mechanical business with additional air con certificates, remapping engine rebuilt

Contact Information for Business Card

Company Name, Director Name, Managing Director, Contact details, email and website

Font styles to use
Serif
Script

```html
<!DOCTYPE html>
<html lang="en">
<head>
<meta charset="utf-8">
<title>KLV Plant Services – Business Card</title>
<link rel="stylesheet" href="https://fonts.googleapis.com/css2?family=Arimo:ital,wght@0,400;0,700;1,400&display=swap">
<style>
  :root {
    --page: #3a3a3c;
    --navy: #0a0c6e;
    --white: #ffffff;
    --ink: #0b0b0b;
    --card-black: #151515;
    --silver: #b9b9bc;
  }
  * { box-sizing: border-box; margin: 0; padding: 0; }
  html, body { width: 1200px; height: 875px; overflow: hidden; }
  body {
    background: var(--page);
    font-family: "Arimo", Arial, sans-serif;
    display: flex;
    flex-direction: column;
    align-items: center;
    justify-content: center;
    gap: 40px;
  }
  .card {
    position: relative;
    width: 630px;
    height: 360px;
    border-radius: 22px;
    overflow: hidden;
  }
  /* back face */
  .card-back {
    background: var(--card-black);
    display: flex;
    align-items: center;
    justify-content: center;
    gap: 18px;
  }
  .card-back .brand-name { color: var(--silver); font-size: 40px; }
  .card-back .brand-dot { border-color: var(--silver); }
  /* brand lockup */
  .brand { display: flex; align-items: center; gap: 14px; }
  .brand-dot {
    width: 34px; height: 34px;
    border: 4px solid var(--navy);
    border-radius: 50%;
  }
  .brand-name { font-weight: 700; font-size: 28px; color: var(--navy); white-space: nowrap; }
  /* front face */
  .card-front { background: var(--navy); }
  .card-front .shape { position: absolute; inset: 0; }
  .card-front .brand { position: absolute; left: 44px; top: 222px; }
  .details {
    position: absolute;
    right: 34px;
    top: 34px;
    text-align: right;
    color: var(--white);
  }
  .person-name { font-weight: 700; font-size: 26px; letter-spacing: 0.5px; }
  .person-title { font-style: italic; font-size: 17px; margin-top: 4px; }
  .rule { width: 110px; height: 2px; background: var(--white); margin: 12px 0 12px auto; }
  .address { font-size: 13.5px; line-height: 1.45; }
  .address strong { font-weight: 700; }
  .contacts { list-style: none; margin-top: 12px; font-size: 14px; line-height: 1.6; }
  .contacts li { display: flex; align-items: center; justify-content: flex-end; gap: 10px; }
  .contacts svg { width: 14px; height: 14px; fill: var(--white); flex: none; }
</style>
</head>
<body>
  <section class="card card-back" aria-label="Card back">
    <div class="brand">
      <span class="brand-dot"></span>
      <span class="brand-name">KLV Plant Services</span>
    </div>
  </section>

  <section class="card card-front" aria-label="Card front">
    <svg class="shape" viewBox="0 0 630 360" aria-hidden="true">
      <path d="M 375 40 A 275 275 0 0 1 310 360" fill="none" stroke="var(--ink)" stroke-width="6"/>
      <circle cx="110" cy="300" r="262" fill="var(--white)"/>
    </svg>

    <div class="brand">
      <span class="brand-dot"></span>
      <span class="brand-name">KLV Plant Services</span>
    </div>

    <div class="details">
      <p class="person-name">DANIEL HARPER</p>
      <p class="person-title">Managing Director</p>
      <div class="rule"></div>
      <p class="address">
        <strong>KLV Plant Services</strong><br>
        18 Foundry Road<br>
        Millbrook, ST, Country, Zip 40217
      </p>
      <ul class="contacts">
        <li>(555) 210-3478
          <svg viewBox="0 0 24 24"><path d="M6.6 10.8a15 15 0 0 0 6.6 6.6l2.2-2.2a1 1 0 0 1 1-.25 11.4 11.4 0 0 0 3.6.57 1 1 0 0 1 1 1V20a1 1 0 0 1-1 1A17 17 0 0 1 3 4a1 1 0 0 1 1-1h3.5a1 1 0 0 1 1 1c0 1.25.2 2.45.57 3.57a1 1 0 0 1-.25 1z"/></svg>
        </li>
        <li>(555) 210-3478
          <svg viewBox="0 0 24 24"><path d="M7 2h10a2 2 0 0 1 2 2v16a2 2 0 0 1-2 2H7a2 2 0 0 1-2-2V4a2 2 0 0 1 2-2zm0 3v13h10V5zm5 14.2a1 1 0 1 0 0 .01z"/></svg>
        </li>
        <li>(555) 210-3478
          <svg viewBox="0 0 24 24"><path d="M6 3h10v5H6zM3 9h18v8h-3v4H6v-4H3zm5 6v4h8v-4z"/></svg>
        </li>
        <li>info@klvplantservices.com
          <svg viewBox="0 0 24 24"><path d="M2 5h20v14H2zm2 2v.5l8 5 8-5V7zm0 2.8V17h16V9.8l-8 5z"/></svg>
        </li>
        <li>klvplantservices.com
          <svg viewBox="0 0 24 24"><path d="M12 2a10 10 0 1 0 0 20 10 10 0 0 0 0-20zm0 2c.9 1.2 1.6 2.8 1.9 5h-3.8c.3-2.2 1-3.8 1.9-5zM4.3 11h3.8a17 17 0 0 0 .3 3H4.9a8 8 0 0 1-.6-3zm11.6 0h3.8a8 8 0 0 1-.6 3h-3.5a17 17 0 0 0 .3-3zm-5.8 0h3.8a15 15 0 0 1-.3 3h-3.2a15 15 0 0 1-.3-3zm.3 5h3.2c-.4 1.7-.9 2.9-1.6 4-.7-1.1-1.2-2.3-1.6-4z"/></svg>
        </li>
      </ul>
    </div>
  </section>
</body>
</html>
```